Veltmoor Capital Stationary Design

We have selected a logo as our winner, we now need a full stationary set to be in the same theme.
Required:
- Letter Head
- Business Card Template
- Custom Envelopes
- A5 Notepad Design (Front cover and content pages. Content pages blank(no lines) but with our branding on them,)
- With Compliments Slip
Updates

Hey All,

We have changed the colour scheme of our logo. Our apologies if anyone has begun designing based off the old scheme. Please see the updated scheme in the brief,

Oliver

Target Market(s)

Target market is experienced property developers and financial institutions.

Industry/Entity Type

Commercial Finance

Font styles to use
Serif

Colors
0054AA
0677BA
7BADD7
CADEEF
E8F1F8
0094D4
00A9DD
6FCCEA
C7EBF8
E9F6FB
00AB8E
00BBA5
67D7C9
C6EFE9
E9F9F6
59FF00
82FF00
B8FF75
E3FFCB
F4FFEA

```html
<!DOCTYPE html>
<html lang="en">
<head>
<meta charset="utf-8">
<title>Veltmoor Capital – Stationery Set</title>
<link rel="stylesheet" href="https://fonts.googleapis.com/css2?family=Libre+Baskerville:wght@400;700&family=Source+Serif+4:wght@400;700&family=Great+Vibes&family=Allura&display=swap">
<style>
  :root{
    --brand-blue:#0E4E9E;
    --band-blue:#0A3AA0;
    --brand-green:#238A3C;
    --ink:#333;
    --paper:#fff;
    --bg:#ECECEC;
    --window:#DADADA;
  }
  *{box-sizing:border-box;margin:0;padding:0}
  html,body{width:1077px;height:1200px;overflow:hidden}
  body{background:var(--bg);position:relative;font-family:"Source Serif 4",serif;color:var(--ink)}
  .sheet{position:absolute;background:var(--paper);box-shadow:0 2px 6px rgba(0,0,0,.18);overflow:hidden}
  .sheet.blue{background:var(--brand-blue)}
  .wordmark{font-family:"Libre Baskerville",serif;font-weight:700;color:var(--brand-blue);letter-spacing:.04em;line-height:1;white-space:nowrap}
  .blue .wordmark,.wordmark.light{color:#fff}
  .center-mark{position:absolute;inset:0;display:flex;align-items:center;justify-content:center}
  .band{position:absolute;left:0;bottom:0;width:100%;display:block}
  .contact{font-size:5px;line-height:7px}
  .contact .ico{color:var(--brand-green);margin-right:2px}

  /* letterhead */
  .letterhead{left:218px;top:98px;width:295px;height:421px}
  .letterhead .wordmark{position:absolute;left:23px;top:30px;font-size:8.5px}
  .letterhead .contact{position:absolute;left:193px;top:18px;padding-left:4px;border-left:.8px solid var(--brand-green)}
  .letter{position:absolute;left:23px;top:94px;width:250px;font-size:5px;line-height:6.3px}
  .letter p{margin-bottom:7px;text-align:justify}
  .letter .salute{font-size:6.5px;font-weight:700;margin:9px 0 8px}
  .letter .sign{font-family:"Allura",cursive;font-size:13px;margin-top:6px}

  /* folder */
  .folder{left:564px;top:85px;width:349px;height:439px}
  .folder .wordmark{font-size:19px}

  /* business cards */
  .card-front{left:111px;top:552px;width:135px;height:76px}
  .card-front .wordmark{position:absolute;left:6px;top:17px;font-size:5px}
  .card-front .person{position:absolute;right:6px;top:11px;text-align:right;font-size:4px;line-height:5px;padding-right:3px;border-right:2px solid var(--brand-green)}
  .card-front .person b{color:var(--brand-blue);font-size:4.2px}
  .card-front .contact{position:absolute;left:5px;bottom:8px;font-size:3.7px;line-height:5px}
  .card-front .addr{position:absolute;right:5px;bottom:9px;font-size:3.7px;line-height:5px;text-align:right}
  .card-back{left:111px;top:649px;width:135px;height:78px}
  .card-back .wordmark{font-size:7px}

  /* envelopes */
  .env-front{left:280px;top:562px;width:330px;height:160px}
  .env-front .wordmark{position:absolute;left:14px;top:26px;font-size:8px}
  .env-front .window{position:absolute;left:211px;top:69px;width:84px;height:33px;background:var(--window)}
  .env-front .contact{position:absolute;left:14px;top:95px;font-size:5.5px;line-height:7.5px}
  .env-back{left:639px;top:562px;width:335px;height:160px}
  .env-back svg.flap{position:absolute;left:0;top:0}
  .env-back .wordmark{position:absolute;left:0;right:0;top:19px;text-align:center;padding-left:60px;font-size:7.5px}

  /* compliments slips */
  .slip-front{left:70px;top:845px;width:340px;height:160px}
  .slip-front .wordmark{position:absolute;left:16px;top:18px;font-size:8.5px}
  .slip-front .contact{position:absolute;left:16px;top:52px;font-size:6px;line-height:8px}
  .slip-front .compliments{position:absolute;right:22px;bottom:34px;font-family:"Great Vibes",cursive;color:var(--brand-green);font-size:22px}
  .slip-back{left:70px;top:1022px;width:340px;height:160px}
  .slip-back .wordmark{font-size:16px}

  /* notepad */
  .note-cover{left:550px;top:827px;width:212px;height:324px}
  .note-cover .wordmark{font-size:11.5px}
  .note-page{left:780px;top:827px;width:212px;height:324px}
  .note-page .wordmark{position:absolute;left:14px;top:20px;font-size:5.5px}
</style>
</head>
<body>

<section class="sheet letterhead">
  <div class="wordmark">VELTMOOR CAPITAL</div>
  <div class="contact">
    42 Fenwick Row<br>Ashford, NY 11402<br>
    <span class="ico">☎</span>555-218-4630<br>
    <span class="ico">✉</span>hello@veltmoorcap.com<br>
    <span class="ico">●</span>www.veltmoorcap.com
  </div>
  <div class="letter">
    <p>Feb-03-2022</p>
    <p>Mr. Peter Lansing<br>President</p>
    <p>Northgate Holdings<br>123 Street Name, Suite# 10<br>City, State, 120023</p>
    <p class="salute">Dear Mr. Peter</p>
    <p>Lorem ipsum dolor sit amet, consectetur adipisicing elit, sed do eiusmod tempor incididunt ut labore et dolore magna aliqua. Ut enim ad minim veniam, quis nostrud exercitation ullamco laboris nisi ut aliquip ex ea commodo consequat. Duis aute irure dolor in reprehenderit in voluptate velit esse cillum dolore eu fugiat nulla pariatur.</p>
    <p>Lorem ipsum dolor sit amet, consectetur adipisicing elit, sed do eiusmod tempor incididunt ut labore et dolore magna aliqua. Ut enim ad minim veniam, quis nostrud exercitation ullamco laboris nisi ut aliquip ex ea commodo consequat. Duis aute irure dolor in reprehenderit in voluptate velit esse cillum dolore eu fugiat nulla pariatur.</p>
    <p>Lorem ipsum dolor sit amet, consectetur adipisicing elit, sed do eiusmod tempor incididunt ut labore et dolore magna aliqua. Ut enim ad minim veniam, quis nostrud exercitation ullamco laboris nisi ut aliquip ex ea commodo consequat.</p>
    <p>Excepteur sint occaecat cupidatat non proident, sunt in culpa qui officia deserunt mollit anim id est laborum. re et dolore magnam aliquam quaerat voluptatem.</p>
    <p style="margin-top:12px">Regards</p>
    <div class="sign">Daniel Harwick</div>
  </div>
  <svg class="band" height="9" viewBox="0 0 100 9" preserveAspectRatio="none">
    <polygon points="0,0 52,0 48,9 0,9" fill="var(--band-blue)"/>
    <polygon points="53,0 100,0 100,9 49,9" fill="var(--brand-green)"/>
  </svg>
</section>

<section class="sheet blue folder">
  <div class="center-mark" style="align-items:flex-start;padding-top:200px"><span class="wordmark">VELTMOOR CAPITAL</span></div>
</section>

<section class="sheet card-front">
  <div class="wordmark">VELTMOOR CAPITAL</div>
  <div class="person"><b>LAURA PENNICK</b><br>Co-Founder</div>
  <div class="contact">
    <span class="ico">☎</span>555-218-4630<br>
    <span class="ico">✉</span>hello@veltmoorcap.com<br>
    <span class="ico">●</span>www.veltmoorcap.com
  </div>
  <div class="addr">42 Fenwick Row<br>Ashford, NY 11402</div>
  <svg class="band" height="4" viewBox="0 0 100 4" preserveAspectRatio="none">
    <polygon points="0,0 52,0 48,4 0,4" fill="var(--band-blue)"/>
    <polygon points="53,0 100,0 100,4 49,4" fill="var(--brand-green)"/>
  </svg>
</section>

<section class="sheet blue card-back">
  <div class="center-mark"><span class="wordmark">VELTMOOR CAPITAL</span></div>
</section>

<section class="sheet env-front">
  <div class="wordmark">VELTMOOR CAPITAL</div>
  <div class="window"></div>
  <div class="contact">
    42 Fenwick Row,<br>Ashford, NY 11402<br>
    <span class="ico">☎</span>555-218-4630<br>
    <span class="ico">✉</span>hello@veltmoorcap.com<br>
    <span class="ico">●</span>www.veltmoorcap.com
  </div>
  <svg class="band" height="8" viewBox="0 0 100 8" preserveAspectRatio="none">
    <polygon points="0,0 49,0 46,8 0,8" fill="var(--band-blue)"/>
    <polygon points="50,0 100,0 100,8 47,8" fill="var(--brand-green)"/>
  </svg>
</section>

<section class="sheet env-back">
  <svg class="flap" width="335" height="48" viewBox="0 0 335 48">
    <path d="M0,0 H335 L323,36 Q319,47 306,47 H29 Q16,47 12,36 Z" fill="var(--brand-blue)"/>
  </svg>
  <div class="wordmark light">VELTMOOR CAPITAL</div>
</section>

<section class="sheet slip-front">
  <div class="wordmark">VELTMOOR CAPITAL</div>
  <div class="contact">
    42 Fenwick Row,<br>Ashford, NY 11402<br>
    <span class="ico">☎</span>555-218-4630<br>
    <span class="ico">✉</span>hello@veltmoorcap.com<br>
    <span class="ico">●</span>www.veltmoorcap.com
  </div>
  <div class="compliments">With Compliments</div>
  <svg class="band" height="8" viewBox="0 0 100 8" preserveAspectRatio="none">
    <polygon points="0,0 48,0 45,8 0,8" fill="var(--band-blue)"/>
    <polygon points="49,0 100,0 100,8 46,8" fill="var(--brand-green)"/>
  </svg>
</section>

<section class="sheet blue slip-back">
  <div class="center-mark"><span class="wordmark">VELTMOOR CAPITAL</span></div>
</section>

<section class="sheet blue note-cover">
  <div class="center-mark"><span class="wordmark">VELTMOOR CAPITAL</span></div>
</section>

<section class="sheet note-page">
  <div class="wordmark">VELTMOOR CAPITAL</div>
  <svg class="band" height="6" viewBox="0 0 100 6" preserveAspectRatio="none">
    <polygon points="0,0 50,0 47,6 0,6" fill="var(--band-blue)"/>
    <polygon points="51,0 100,0 100,6 48,6" fill="var(--brand-green)"/>
  </svg>
</section>

</body>
</html>
```